Wellness, Meaning, and the Inner Journey Research Program Website

Overview: This website will serve a new research program (Wellness, Meaning, and the Inner Journey) at the Harrowgate University School of Medicine. I want a clean, intuitive design that has a navigation bar, but uses icons/graphic buttons to link to the main pages. In an attached Word document, I have provided a basic information architecture for the site, understanding that this project would just generate graphics and code for the 3 pages. I highlighted the 3 pages I'd like designed.
Target market: People who want to participate in our research, or contribute grant funding to specific projects.
Number of page: The design project focuses on 3 pages, but the site must accommodate 6 pages with top-level links. See attached Word doc.
Logo and website header: Please integrate our logo in the header. I've uploaded it as a png file--both with the name of the website and with just the logo image. I imaging the logo would look great in a banner set against an image of a mountain. The two main design themes I want to see included are nature and healthcare.
Text content: I have not yet provided text. Use some dummy text.
Technical Specifications:
- Build using WordPress. We will host this site ourselves on NetHarbor using WordPress.
- The design package must be coded.
- The template must be responsive to different platforms (e.g., computer, mobile phone, iPad).
Thank you! I look forward to seeing your designs.
- Ned

```html
<!DOCTYPE html>
<html lang="en">
<head>
<meta charset="utf-8">
<title>Wellness, Meaning, and the Inner Journey — Research Program</title>
<link href="https://fonts.googleapis.com/css2?family=Poppins:wght@300;400;500;600;700&family=Archivo:wght@700;800&family=Montserrat:wght@700;800&display=swap" rel="stylesheet">
<style>
:root{
  --mint:#e7f7f2;
  --blue:#0b4f9f;
  --blue-dark:#083c7a;
  --green:#1ba679;
  --teal:#17a58a;
  --ink:#1d1d1d;
  --muted:#666f72;
  --white:#ffffff;
  --footer:#071719;
  --line:#1d5fa8;
}
*{box-sizing:border-box;margin:0;padding:0}
html,body{width:1200px;height:4525px;overflow:hidden}
body{position:relative;background:var(--mint);font-family:"Poppins",sans-serif;color:var(--ink)}
.abs{position:absolute}
a{text-decoration:none;color:inherit}

/* header */
.hero{position:absolute;left:0;top:0;width:1200px;height:715px;overflow:hidden}
.hero-photo{position:absolute;inset:0;background:
  linear-gradient(180deg,#f3f6f7 0%,#e7edf0 22%,#cfdbe4 42%,#8ea6bb 58%,#e9eef2 70%,#b9c6d3 85%,#6d8398 100%)}
.hero-wave{position:absolute;left:0;bottom:0}
.brand{position:absolute;left:60px;top:22px;display:flex;align-items:center;gap:10px}
.brand-dot{width:44px;height:44px;border-radius:50%;background:var(--green)}
.brand-name{font-size:11.5px;font-weight:600;color:var(--blue);line-height:15px}
.brand-name small{display:block;color:var(--green);font-size:9px;font-weight:500}
.nav{position:absolute;left:515px;top:28px;display:flex;align-items:center;gap:20px;font-size:12.5px}
.nav a.active{background:var(--blue);color:#fff;padding:7px 17px;border-radius:7px}
.call{position:absolute;left:940px;top:24px;display:flex;gap:10px;align-items:center}
.call small{display:block;font-size:10px;color:#555}
.call b{font-size:19px;font-weight:500}
.hero-title{position:absolute;left:0;width:1200px;text-align:center;font-family:"Archivo",sans-serif;font-weight:800;font-size:46px;line-height:56px}
.hero-title.green{top:232px;color:var(--green)}
.hero-title.dark{top:288px;color:#111}
.hero-sub{position:absolute;top:358px;left:0;width:1200px;text-align:center;font-size:14.5px;font-weight:500;line-height:21px}
.pill{position:absolute;width:120px;height:120px;border-radius:50%;background:var(--teal);color:#fff;border:4px solid #fff;display:flex;flex-direction:column;align-items:center;justify-content:center;font-size:13px;gap:6px}
.pill.blue{background:var(--blue)}
.follow{position:absolute;left:1160px;top:580px;transform:rotate(-90deg);transform-origin:left top;font-size:10px;color:#fff;white-space:nowrap}
.social-v{position:absolute;left:1162px;display:flex;flex-direction:column;gap:10px;top:600px}
.social-v span{width:14px;height:14px;border-radius:50%;background:#fff}

/* shared headings */
.mark{width:46px;height:46px;border-radius:50%;background:var(--green);opacity:.9}
.sec-title{font-size:34px;font-weight:500;color:var(--blue)}
.sec-sub{font-size:15px;color:var(--green)}
.center{position:absolute;left:0;width:1200px;text-align:center}
.copy{font-size:11.5px;color:var(--muted);line-height:20px}
.more{font-size:12.5px;color:var(--teal);font-weight:500;text-decoration:underline;display:inline-flex;align-items:center;gap:8px}

/* cards */
.card{position:absolute;top:942px;width:292px;height:314px;background:#fff;border-radius:10px;box-shadow:0 6px 22px rgba(10,80,70,.08);text-align:center;padding:32px 24px}
.card-icon{width:92px;height:92px;margin:0 auto;border-radius:50%;background:linear-gradient(135deg,#cfeee2,#9fd6e2)}
.card h3{margin-top:24px;font-size:17px;font-weight:500;color:var(--blue)}
.card p{margin-top:14px;font-size:11px;line-height:20px;color:var(--muted)}

/* timeline */
.tl-line{position:absolute;left:599px;top:1505px;width:2px;height:935px;background:var(--line)}
.tl-end{position:absolute;left:595px;width:10px;height:10px;border-radius:50%;background:var(--line)}
.tl-node{position:absolute;left:586px;width:28px;height:28px;border-radius:50%;border:2px solid var(--line);background:var(--mint)}
.tl-node::after{content:"";position:absolute;inset:6px;border-radius:50%;background:var(--green);opacity:.6}
.photo{position:absolute}
.tl-title{font-size:28px;font-weight:500;color:var(--blue)}

/* projects */
.btn{position:absolute;left:990px;top:2535px;width:150px;height:39px;background:var(--blue);color:#fff;border-radius:7px;font-size:13.5px;font-weight:500;display:flex;align-items:center;justify-content:center}
.coach{position:absolute;left:383px;top:2675px;font-family:"Montserrat",sans-serif;font-weight:800;font-size:28px;line-height:34px;color:#102036;letter-spacing:1px}
.frame{position:absolute;border:1px solid rgba(255,255,255,.6);color:#fff;font-family:"Montserrat",sans-serif;font-weight:700;font-size:22px;display:flex;align-items:center;justify-content:center}

/* faq */
.faq{position:absolute;width:340px}
.faq-num{position:absolute;width:40px;height:40px;border-radius:50%;background:radial-gradient(circle at 35% 30%,#3a86d6,var(--blue));color:#fff;font-size:16px;display:flex;align-items:center;justify-content:center;box-shadow:0 0 0 3px #cfe1f2}
.faq h4{font-size:15px;font-weight:500;line-height:22px;margin-bottom:10px}
.faq-rule{position:absolute;width:1px;height:105px;background:#8fb0d0}

/* newsletter */
.news{position:absolute;left:0;top:3769px;width:1200px;height:396px;overflow:hidden}
.news-bg{position:absolute;inset:0;background:radial-gradient(circle at 82% 40%,#dbe9e6 0%,#9fbcc0 22%,#2a7f86 45%,#0d6b70 70%,#0a4f57 100%)}
.field{position:absolute;top:4040px;height:40px;background:#fff;border-radius:6px;font-size:11px;color:#555;padding:0 14px;display:flex;align-items:center}
.subscribe{position:absolute;left:813px;top:4040px;width:112px;height:40px;border-radius:6px;background:var(--blue);color:#fff;font-size:12.5px;font-weight:500;display:flex;align-items:center;justify-content:center}

/* footer */
.footer{position:absolute;left:0;top:4165px;width:1200px;height:360px;background:var(--footer);color:#fff}
.f-social{position:absolute;top:4335px;left:537px;display:flex;gap:9px}
.f-social span{width:36px;height:36px;border-radius:50%;border:2px solid var(--green)}
.f-line{font-size:11.5px}
</style>
</head>
<body>

<section class="hero">
  <div class="hero-photo" role="img" aria-label="Snowy mountain range with a climber in a red jacket standing on a peak, a misty meditating figure and a stethoscope faded into the sky"></div>
  <svg class="hero-wave" width="1200" height="120" viewBox="0 0 1200 120">
    <path d="M0 95 C300 60 500 120 720 90 C900 66 1050 80 1200 62 L1200 120 L0 120 Z" fill="var(--mint)"/>
  </svg>
</section>

<header>
  <div class="brand"><span class="brand-dot"></span>
    <div class="brand-name">Wellness, Meaning, and the Inner Journey<small>The Research Program</small></div></div>
  <nav class="nav">
    <a class="active">Home</a><a>People</a><a>Projects</a><a>FAQs</a><a>Resources</a><a>Contact</a>
  </nav>
  <div class="call">
    <svg width="30" height="30" viewBox="0 0 24 24"><path d="M6.6 10.8a15 15 0 006.6 6.6l2.2-2.2a1 1 0 011-.25 11.4 11.4 0 003.6.57 1 1 0 011 1V20a1 1 0 01-1 1A17 17 0 013 4a1 1 0 011-1h3.5a1 1 0 011 1c0 1.25.2 2.45.57 3.57a1 1 0 01-.25 1z" fill="var(--green)"/></svg>
    <div><small>Call Us On :</small><b>+1 555 010 2040</b></div>
  </div>
</header>

<h1 class="hero-title green">RESEARCH PROGRAM</h1>
<h2 class="hero-title dark">FOR THE BRIGHT FUTURE !</h2>
<p class="hero-sub">We serve a new RESEARCH PROGRA at the Harrowgate University<br>School of Medicine</p>

<a class="pill" style="left:405px;top:598px">
  <svg width="42" height="36" viewBox="0 0 42 36"><path d="M21 33 C6 22 2 15 2 10 A8 8 0 0121 7 A8 8 0 0140 10 C40 15 36 22 21 33Z" fill="none" stroke="#fff" stroke-width="2.5"/></svg>Healthcare</a>
<a class="pill blue" style="left:540px;top:570px">
  <svg width="48" height="36" viewBox="0 0 48 36"><path d="M12 3h24l9 10-21 20L3 13z M3 13h42 M18 3l6 30 6-30" fill="none" stroke="#fff" stroke-width="2.3"/></svg>Values</a>
<a class="pill" style="left:675px;top:598px">
  <svg width="40" height="38" viewBox="0 0 40 38"><circle cx="20" cy="20" r="7" fill="none" stroke="#fff" stroke-width="2.3"/><path d="M20 2v6M20 32v5M4 20h6M30 20h6M8 8l4 4M28 28l4 4M32 8l-4 4" stroke="#fff" stroke-width="2.3"/></svg>Spiritual Life</a>

<div class="follow">Follow Us On</div>
<div class="social-v"><span></span><span></span><span></span></div>

<section>
  <div class="mark abs" style="left:135px;top:790px"></div>
  <h2 class="sec-title abs" style="left:203px;top:785px">Our Vision</h2>
  <p class="sec-sub abs" style="left:204px;top:838px;line-height:25px">Wellness, Meaning, and the Inner Journey<br>The Research Program</p>
  <p class="copy abs" style="left:636px;top:792px;width:430px;font-size:11px">Lorem Ipsum has been the industry's standard dummy text ever since the 1500s, when an unknown printer took a galley of type and scrambled it to make a type specimen book. It has survived not only five centuries, but also the leap into electronic typesetting, remaining.</p>

  <div class="card" style="left:139px">
    <div class="card-icon" role="img" aria-label="Illustration of a caregiver figure"></div>
    <h3>People</h3>
    <p>Lorem Ipsum has been the industry's standard dummy text ever since the 1500s, when an unknown printer took a galley of type and scrambled.</p>
  </div>
  <div class="card" style="left:454px">
    <div class="card-icon" role="img" aria-label="Illustration of a gear with a growing leaf"></div>
    <h3>Research Projects</h3>
    <p>Lorem Ipsum has been the industry's standard dummy text ever since the 1500s, when an unknown printer took a galley of type and scrambled.</p>
  </div>
  <div class="card" style="left:769px">
    <div class="card-icon" role="img" aria-label="Illustration of a person with a question bubble"></div>
    <h3>FAQs</h3>
    <p>Lorem Ipsum has been the industry's standard dummy text ever since the 1500s, when an unknown printer took a galley of type and scrambled.</p>
  </div>
</section>

<section>
  <div class="mark abs" style="left:577px;top:1336px"></div>
  <h2 class="sec-title center" style="top:1383px">People</h2>
  <p class="sec-sub center" style="top:1432px;font-size:14px">Wellness, Meaning, and the Inner Journey</p>

  <div class="tl-line"></div>
  <div class="tl-end" style="top:1500px"></div>
  <div class="tl-end" style="top:2436px"></div>

  <div class="photo" style="left:139px;top:1505px;width:405px;height:243px;background:linear-gradient(120deg,#3b3f46,#8a7a62 45%,#d9c7a0 60%,#6d6a66)" role="img" aria-label="Team of researchers holding glowing light bulbs together"></div>
  <div class="tl-node" style="top:1554px"></div>
  <h3 class="tl-title abs" style="left:655px;top:1548px">Research Team</h3>
  <p class="copy abs" style="left:657px;top:1596px;width:360px">Lorem Ipsum has been the industry's standard dummy text ever since the 1500s, when an unknown printer took a galley of type and scrambled Lorem Ipsum has been.</p>
  <a class="more abs" style="left:659px;top:1668px">Read More <svg width="22" height="10"><path d="M0 5h20M15 1l5 4-5 4" fill="none" stroke="currentColor" stroke-width="1.5"/></svg></a>

  <div class="tl-node" style="top:1884px"></div>
  <h3 class="tl-title abs" style="left:139px;top:1877px;width:404px;text-align:right">Advisory committee</h3>
  <p class="copy abs" style="left:183px;top:1925px;width:360px;text-align:right">Lorem Ipsum has been the industry's standard dummy text ever since the 1500s, when an unknown printer took a galley of type and scrambled Lorem Ipsum has been.</p>
  <a class="more abs" style="left:444px;top:2001px">Read More <svg width="22" height="10"><path d="M0 5h20M15 1l5 4-5 4" fill="none" stroke="currentColor" stroke-width="1.5"/></svg></a>
  <div class="photo" style="left:656px;top:1832px;width:405px;height:243px;background:linear-gradient(160deg,#e6eef5,#9fb4cc 40%,#2c4f86 70%,#142d57)" role="img" aria-label="Conference hall with an audience facing presentation screens"></div>

  <div class="photo" style="left:139px;top:2158px;width:405px;height:244px;background:linear-gradient(150deg,#1e2b20,#3d4f3a 50%,#6f6d57)" role="img" aria-label="Partner organisation badges over a dark forest waterfall">
    <div class="abs" style="left:48px;top:50px;width:150px;height:70px;background:#fff"></div>
    <div class="abs" style="left:204px;top:50px;width:150px;height:70px;background:#fff"></div>
    <div class="abs" style="left:126px;top:126px;width:150px;height:70px;background:#fff"></div>
  </div>
  <div class="tl-node" style="top:2208px"></div>
  <h3 class="tl-title abs" style="left:655px;top:2201px">Partners</h3>
  <p class="copy abs" style="left:657px;top:2249px;width:360px">Lorem Ipsum has been the industry's standard dummy text ever since the 1500s, when an unknown</p>
  <a class="more abs" style="left:659px;top:2300px">Read More <svg width="22" height="10"><path d="M0 5h20M15 1l5 4-5 4" fill="none" stroke="currentColor" stroke-width="1.5"/></svg></a>
</section>

<section>
  <div class="mark abs" style="left:60px;top:2525px"></div>
  <h2 class="sec-title abs" style="left:126px;top:2516px">Projects</h2>
  <p class="sec-sub abs" style="left:127px;top:2566px">Wellness, Meaning, and the Inner Journey</p>
  <a class="btn">View All Projects</a>

  <div class="photo" style="left:0;top:2627px;width:600px;height:527px;background:linear-gradient(180deg,#e8f2f5 0%,#c9dde8 30%,#5f86b0 55%,#1f3d78 75%,#0f2350 100%)" role="img" aria-label="Person meditating on a hill overlooking a blue valley"></div>
  <div class="coach">YOUR<br>PERSONAL<br>SPIRITUAL<br>COACH</div>

  <div class="photo" style="left:600px;top:2627px;width:600px;height:263px;background:linear-gradient(180deg,#3a2d36,#7a4a3c 45%,#d9743a 70%,#3a2a28)" role="img" aria-label="Broken chain with birds flying into a sunset"></div>
  <div class="frame" style="left:770px;top:2721px;width:220px;height:68px">Turn Your Life Up</div>

  <div class="photo" style="left:600px;top:2890px;width:600px;height:264px;background:linear-gradient(135deg,#2e3a24,#55663e 45%,#8a8f6a 60%,#2b3320)" role="img" aria-label="Hiker looking up at a giant tree trunk in a forest"></div>
  <div class="frame" style="left:775px;top:2977px;width:270px;height:68px">Beyond Religion</div>
</section>

<section>
  <div class="mark abs" style="left:577px;top:3226px"></div>
  <h2 class="sec-title center" style="top:3276px">Faq's</h2>
  <p class="sec-sub center" style="top:3325px;font-size:14px">Wellness, Meaning, and the Inner Journey</p>

  <div class="faq-num" style="left:136px;top:3392px">1</div>
  <div class="faq-rule" style="left:156px;top:3442px"></div>
  <div class="faq" style="left:204px;top:3390px">
    <h4>What makes this project unique?</h4>
    <p class="copy" style="font-size:11px">Lorem Ipsum has been the industry's standard dummy text ever since the when an unknown printer took a galley of type and scrambled has been.</p>
    <a class="more" style="margin-top:10px;margin-left:3px">Read More <svg width="22" height="10"><path d="M0 5h20M15 1l5 4-5 4" fill="none" stroke="currentColor" stroke-width="1.5"/></svg></a>
  </div>

  <div class="faq-num" style="left:136px;top:3549px">2</div>
  <div class="faq" style="left:204px;top:3547px">
    <h4>Does this project assume that the impact of religion is always positive?</h4>
    <p class="copy" style="font-size:11px">Lorem Ipsum has been the industry's standard dummy text ever since the when an unknown printer took a galley of type and scrambled has been.</p>
    <a class="more" style="margin-top:10px;margin-left:3px">Read More <svg width="22" height="10"><path d="M0 5h20M15 1l5 4-5 4" fill="none" stroke="currentColor" stroke-width="1.5"/></svg></a>
  </div>

  <div class="faq-num" style="left:616px;top:3392px">3</div>
  <div class="faq-rule" style="left:636px;top:3442px"></div>
  <div class="faq" style="left:684px;top:3390px">
    <h4>How can I collaborate?</h4>
    <p class="copy" style="font-size:11px">Lorem Ipsum has been the industry's standard dummy text ever since the when an unknown printer took a galley of type and scrambled has been.</p>
    <a class="more" style="margin-top:10px;margin-left:3px">Read More <svg width="22" height="10"><path d="M0 5h20M15 1l5 4-5 4" fill="none" stroke="currentColor" stroke-width="1.5"/></svg></a>
  </div>

  <div class="faq-num" style="left:616px;top:3549px">4</div>
  <div class="faq" style="left:684px;top:3547px">
    <h4>Will Harrowgate faculty lead all projects?</h4>
    <p class="copy" style="font-size:11px">Lorem Ipsum has been the industry's standard dummy text ever since the when an unknown printer took a galley of type and scrambled has been.</p>
    <a class="more" style="margin-top:10px;margin-left:3px">Read More <svg width="22" height="10"><path d="M0 5h20M15 1l5 4-5 4" fill="none" stroke="currentColor" stroke-width="1.5"/></svg></a>
  </div>
</section>

<section class="news">
  <div class="news-bg" role="img" aria-label="Soft teal bokeh background with a dandelion seed head on the right"></div>
  <svg class="abs" style="left:0;top:0" width="1200" height="40" viewBox="0 0 1200 40"><path d="M0 0H1200V10C1000 34 800 4 600 20 400 36 200 8 0 24Z" fill="var(--mint)"/></svg>
</section>
<div class="abs" style="left:577px;top:3820px;width:46px;height:46px;border-radius:50%;background:#fff;opacity:.85"></div>
<h2 class="center" style="top:3878px;font-size:35px;font-weight:500;color:#fff;line-height:44px">Learn More About Spiritual<br>Traditions !</h2>
<p class="center" style="top:3977px;font-size:11.5px;color:#eef;line-height:20px">Lorem Ipsum has been the industry's standard dummy text ever since the when an unknown<br>printer took a galley of type and scrambled has been.</p>
<div class="field" style="left:273px;width:263px">Enter Email *</div>
<div class="field" style="left:543px;width:263px">Enter Name *</div>
<a class="subscribe">SUBSCRIBE</a>

<footer class="footer">
  <div class="abs" style="left:0;top:58px;width:1200px;display:flex;flex-direction:column;align-items:center;gap:8px">
    <span style="width:60px;height:60px;border-radius:50%;background:var(--green)"></span>
    <span style="font-size:13px;font-weight:600;color:var(--green)">WMIJ Research</span>
  </div>
</footer>
<div class="f-social"><span></span><span></span><span></span></div>
<p class="center f-line" style="top:4398px;color:#fff"><span style="color:var(--blue)">Phone :</span> 555 0142 388 &nbsp;|&nbsp; <span style="color:var(--blue)">Email :</span> hello@wmij-research.org</p>
<p class="center f-line" style="top:4430px;color:#fff">Home &nbsp;|&nbsp; People &nbsp;|&nbsp; Projects &nbsp;|&nbsp; Faq's &nbsp;|&nbsp; Resources &nbsp;|&nbsp; Contact</p>
<p class="center f-line" style="top:4452px;color:#ccc;font-size:11px"><span style="color:var(--green)">©WMIJ Research Program</span> - 2021 All rights reserved</p>

</body>
</html>
```